WE ARE BRIGHT SPARROW, building a full website with ecommerce

requirements:
CODED FOR SITEQUILL
ONLINE STORE FUNCTION WITH E-COMMERCE USING TRADEBLOOM
PAGEWAVE AND PICTOLANE LINKS

I need a website design for my organization, WE ARE BRIGHT SPARROW, a global empowerment movement elevating woman, and the world. The site's home page should reflect our mission, to empower women. It should have a strong, empowering feel, with minimalistic design.
Please see www.lunavelto.com and http://www.corvenhal.co/ for an inspiration on layout and feel.

**PLEASE SEE ATTACHMENT "LOGO MOCK UP" FOR LOGO. THIS IS NOT THE FINAL VECTOR FILE, BUT THIS LOOKS THE SAME AS THE FINAL LOGO.

HOME PAGE:
The first section of the home page should include a background image with our logo center.

You should include the following links to pages at the top right of the page:
MISSION
MANTRA
ARMOR
MEET BS (I would like "bs" to be our logo)
pagewave and pictolane links

As you scroll down the page, you should see the following sections, which correlate to the links to pages as written above. **SEE ATTACHED SKETCH "HOMEPAGE LAYOUT IDEA" FOR REFERENCE**

WHO WE ARE (correlates to the link Mission)

OUR MANTRA (correlates to the link Mantra)

OUR ARMOR (correlates to the link The Shirt)
(This is where we will sell a shirt (and other apparel) and need the e-commerce function)

MEET BRIGHT SPARROWS (correlates to the link Meet BS)

SHOW OFF YOUR SUPER POWERS (correlates to the pagewave and pictolane)

FEATURED BRIGHT SPARROW (no link on top right of page)

On the homepage, for each of the above sections, as you scroll down there should be an image, either in the background or framed, next to the title (WHO WE ARE, for example), as well as one sentence of small text explaining the title. The title (WHO WE ARE) and the one sentence should link to a page (ie WHO WE ARE + the one sentence links to the MISSION page). ** SEE ATTACHED SKETCH "HOMEPAGE SECTION IDEAS" FOR REFERENCE**

**PLEASE SEE ATTACHMENT "WEBSITE TITLE IDEAS" FOR A STARTING PLACE OF THE LOOK. These don't have to be exact, but they give you an idea of what I'm looking for.

**FONTS TYPOLD EXTRA BOLD AND TYPOLD BOOK 500 (WHICH SHOULD BE BOLDED MANUALLY) ARE ATTACHED**

Target Market(s)

Women, mainly in US

Industry/Entity Type

Social

Coding

Coded - Design and coding required

Number of Pages Required

5+ page

Font styles to use
Other font styles liked:
• Typol Extra Bold

Requirements
Must have
• CODED FOR SITEQUILL
• ONLINE STORE FUNCTION WITH E-COMMERCE USING TRADEBLOOM
• PAGEWAVE AND PICTOLANE LINKS
• Typold Extra Bold and Typold Book 500, attached
• please see description for all requirements
Nice to have
• please see description for all ideas
Should not have

```html
<!DOCTYPE html>
<html lang="en">
<head>
<meta charset="utf-8">
<title>WE ARE BRIGHT SPARROW</title>
<link rel="stylesheet" href="https://fonts.googleapis.com/css2?family=Montserrat:wght@400;500;600;700;800&family=Open+Sans:wght@400;600&display=swap">
<style>
:root{
  --ink:#111111;
  --white:#ffffff;
  --sky:#1ab4e8;
  --sky-deep:#0a8fd0;
  --sky-light:#49c8f2;
  --gray:#e8e8e8;
  --text:#444444;
  --line:#bdbdbd;
}
*{box-sizing:border-box;margin:0;padding:0}
html,body{width:1200px;height:3727px;overflow:hidden;background:var(--white)}
body{position:relative;font-family:"Open Sans",Arial,sans-serif;color:var(--ink)}
a{color:inherit;text-decoration:none}
section,header,footer{position:absolute;left:0;width:1200px}
.photo{position:absolute}

/* header */
.site-header{top:0;height:105px;background:var(--white)}
.brand{position:absolute;left:122px;top:26px;display:flex;align-items:center;gap:12px;font-family:"Montserrat",sans-serif;font-weight:800;font-size:19px;line-height:19px;width:220px}
.brand-square{width:34px;height:34px;border:4px solid var(--ink);flex:none}
.main-nav{position:absolute;left:482px;top:40px;display:flex;gap:50px;font-family:"Montserrat",sans-serif;font-weight:500;font-size:16px;letter-spacing:.5px}
.social-nav{position:absolute;left:985px;top:40px;display:flex;gap:16px;font-family:"Montserrat",sans-serif;font-weight:700;font-size:11px}

/* hero */
.hero{top:105px;height:557px;background:linear-gradient(100deg,#5f6a3a 0%,#8a7452 30%,#6b5a4a 55%,#a56a52 75%,#70613f 100%)}
.hero-shade{position:absolute;inset:0;background:rgba(20,20,20,.28)}
.hero-mark{position:absolute;left:570px;top:110px;width:60px;height:60px;border:6px solid var(--white)}
.hero-title{position:absolute;left:0;width:1200px;top:225px;text-align:center;color:var(--white);font-family:"Montserrat",sans-serif;font-weight:800;font-size:52px;line-height:58px}
.hero-sub{position:absolute;left:0;width:1200px;top:288px;text-align:center;color:var(--white);font-family:"Montserrat",sans-serif;font-weight:800;font-size:37px}
.signup{position:absolute;left:290px;top:355px;display:flex;height:45px}
.signup-field{width:460px;background:var(--white);font-size:16px;color:#888;padding:12px 14px}
.signup-btn{width:152px;background:var(--sky);color:var(--white);font-family:"Montserrat",sans-serif;font-weight:700;font-size:15px;text-align:center;line-height:45px}
.arrow{position:absolute;top:222px}
.arrow-left{left:84px}
.arrow-right{left:1088px}

/* mission band */
.mission-band{top:662px;height:188px;background:linear-gradient(110deg,var(--sky-light),var(--sky) 45%,var(--sky-deep))}
.band-text{position:absolute;top:35px;left:0;width:1200px;text-align:center;color:var(--white);font-family:"Montserrat",sans-serif;font-weight:500;font-size:27px;line-height:30px;letter-spacing:2px}
.band-cta{position:absolute;top:110px;left:0;width:1200px;text-align:center;color:var(--white);font-family:"Montserrat",sans-serif;font-weight:800;font-size:34px;line-height:40px}

/* feature blocks */
.feature{position:absolute}
.feature-title{display:flex;align-items:center;gap:14px;font-family:"Montserrat",sans-serif;font-weight:800}
.title-square{width:56px;height:56px;border:6px solid currentColor;flex:none}
.title-small{display:block;font-size:27px;line-height:28px;font-weight:700}
.title-big{display:block;font-size:42px;line-height:42px}
.feature p{margin-top:18px;width:470px;font-size:15px;line-height:26px;color:var(--text)}
.dark .feature p{color:#dddddd}

.who{top:850px;height:450px;background:var(--white)}
.mantra{top:1300px;height:453px;background:var(--gray)}
.meet{top:1753px;height:517px;background:#000000;color:var(--white)}
.armor{top:2270px;height:540px;background:var(--white)}
.power{top:2810px;height:283px;background:var(--gray)}
.featured{top:3093px;height:467px;background:var(--white)}

/* armor */
.armor-title{position:absolute;left:0;width:1200px;top:45px;display:flex;justify-content:center}
.product{position:absolute;top:135px;width:281px;height:341px;border:2px solid var(--line);background:var(--white)}
.product-shot{position:absolute;left:40px;top:20px;width:200px;height:200px}
.product-name{position:absolute;left:34px;top:242px;font-family:"Montserrat",sans-serif;font-weight:800;font-size:15px}
.product-price{position:absolute;left:34px;top:276px;font-family:"Montserrat",sans-serif;font-size:27px}
.buy{position:absolute;left:150px;top:280px;width:105px;height:32px;background:var(--ink);color:var(--white);font-family:"Montserrat",sans-serif;font-weight:700;font-size:11px;text-align:center;line-height:32px}

/* power */
.power-title{position:absolute;left:221px;top:90px}
.social-tile{position:absolute;top:95px;height:106px;display:flex;align-items:center;gap:10px;font-family:"Montserrat",sans-serif;font-weight:800;font-size:18px}
.tile-square{width:60px;height:60px;border:5px solid var(--ink);border-radius:10px}

/* footer */
.site-footer{top:3560px;height:167px;background:#000000;color:var(--white)}
.footer-mark{position:absolute;left:578px;top:-22px;width:44px;height:44px;background:var(--white);border:5px solid #000}
.footer-nav{position:absolute;left:0;width:1200px;top:42px;display:flex;justify-content:center;gap:70px;font-family:"Montserrat",sans-serif;font-weight:500;font-size:16px}
.copyright{position:absolute;left:0;width:1200px;top:90px;text-align:center;font-size:11px;color:#cccccc}
</style>
</head>
<body>

<header class="site-header">
  <a class="brand" href="#"><span class="brand-square"></span><span>WE ARE BRIGHT SPARROW</span></a>
  <nav class="main-nav">
    <a href="#mission">MISSION</a><a href="#mantra">MANTRA</a><a href="#meet">MEET BS</a><a href="#armor">ARMOR</a>
  </nav>
  <nav class="social-nav"><a href="#">PAGEWAVE</a><a href="#">PICTOLANE</a></nav>
</header>

<section class="hero">
  <div class="photo" style="inset:0" role="img" aria-label="Group of smiling women outdoors"></div>
  <div class="hero-shade"></div>
  <div class="hero-mark"></div>
  <h1 class="hero-title">WE ARE BRIGHT SPARROW</h1>
  <div class="hero-sub">AND I WILL CONQUER THE WORLD</div>
  <form class="signup"><div class="signup-field">brightsparrow@email.com</div><div class="signup-btn">LET'S FLY</div></form>
  <svg class="arrow arrow-left" width="30" height="60" viewBox="0 0 30 60"><polyline points="26,2 4,30 26,58" fill="none" stroke="#fff" stroke-width="3"/></svg>
  <svg class="arrow arrow-right" width="30" height="60" viewBox="0 0 30 60"><polyline points="4,2 26,30 4,58" fill="none" stroke="#fff" stroke-width="3"/></svg>
</section>

<section class="mission-band">
  <p class="band-text">WE ARE BRIGHT SPARROW IS A GLOBAL EMPOWERMENT<br>MOVEMENT ELEVATING WOMEN... AND THE WORLD.</p>
  <div class="band-cta">LET'S FLY</div>
</section>

<section class="who" id="mission">
  <a class="feature" href="#" style="left:122px;top:68px">
    <div class="feature-title"><span class="title-square"></span><span><span class="title-small">WHO WE</span><span class="title-big">ARE</span></span></div>
    <p>Vivamus porttitor purus nisi eleifend libero a tempus libero lectus feugiat felis Morbi diam mauris viverra in gravida eu mattis in ante Morbi eget arcu Morbi porta libero id ullamcorper</p>
    <p style="margin-top:6px">lacus mollis aliquam Curabitur iaculis tempus eros Curabitur vel mi sit amet magna malesuada ultrices</p>
  </a>
  <div class="photo" style="left:636px;top:72px;width:447px;height:293px;background:linear-gradient(135deg,#d9d4cc,#8c7766 55%,#c9c2b8)" role="img" aria-label="Women working together around a table"></div>
</section>

<section class="mantra" id="mantra">
  <div class="photo" style="left:122px;top:77px;width:447px;height:295px;background:radial-gradient(circle at 50% 40%,#6a6a6a,#2f2f2f)" role="img" aria-label="Woman in a suit before a chalkboard drawing of strong arms"></div>
  <a class="feature" href="#" style="left:616px;top:77px">
    <div class="feature-title"><span class="title-square"></span><span><span class="title-small">OUR</span><span class="title-big">MANTRA</span></span></div>
    <p>Vivamus porttitor purus nisi eleifend libero a tempus libero lectus feugiat felis Morbi diam mauris viverra in gravida eu mattis in ante Morbi eget arcu Morbi porta libero id ullamcorper</p>
    <p style="margin-top:6px">lacus mollis aliquam Curabitur iaculis tempus eros Curabitur vel mi sit amet magna malesuada ultrices</p>
  </a>
</section>

<section class="meet dark" id="meet">
  <a class="feature" href="#" style="left:122px;top:97px">
    <div class="feature-title"><span class="title-square"></span><span><span class="title-small">MEET BRIGHT</span><span class="title-big">SPARROW</span></span></div>
    <p>Vivamus porttitor purus nisi eleifend libero a tempus libero lectus feugiat felis Morbi diam mauris viverra in gravida eu mattis in ante Morbi eget arcu Morbi porta libero id ullamcorper</p>
    <p style="margin-top:6px">lacus mollis aliquam Curabitur iaculis tempus eros Curabitur vel mi sit amet magna malesuada ultrices</p>
  </a>
  <div class="photo" style="left:639px;top:106px;width:447px;height:296px;background:linear-gradient(160deg,#5a4a40,#2a2420 50%,#6b5648)" role="img" aria-label="Large crowd of women in dark business clothes"></div>
</section>

<section class="armor" id="armor">
  <div class="armor-title"><div class="feature-title"><span class="title-square" style="width:46px;height:46px;border-width:5px"></span><span><span class="title-small" style="font-size:22px;line-height:22px">OUR</span><span class="title-big" style="font-size:34px;line-height:34px">ARMOR</span></span></div></div>
  <article class="product" style="left:147px">
    <div class="product-shot" style="background:radial-gradient(circle,#2a2a2a 55%,#fff 72%)" role="img" aria-label="Black t-shirt"></div>
    <div class="product-name">TSHIRT TITTLE</div><div class="product-price">$15.99</div><a class="buy" href="#">BUY NOW</a>
  </article>
  <article class="product" style="left:447px">
    <div class="product-shot" style="background:radial-gradient(circle,#d9221e 55%,#fff 72%)" role="img" aria-label="Red t-shirt"></div>
    <div class="product-name">TSHIRT TITTLE</div><div class="product-price">$15.99</div><a class="buy" href="#">BUY NOW</a>
  </article>
  <article class="product" style="left:753px">
    <div class="product-shot" style="background:radial-gradient(circle,#f3c51a 50%,#fff 68%)" role="img" aria-label="Yellow women's t-shirt"></div>
    <div class="product-name" style="top:255px">TSHIRT TITTLE</div><div class="product-price" style="top:283px">$15.99</div><a class="buy" href="#" style="top:290px">BUY NOW</a>
  </article>
</section>

<section class="power">
  <div class="power-title feature-title"><span class="title-square"></span><span><span class="title-small" style="font-size:24px;line-height:26px">SHOW OFF YOUR</span><span class="title-big" style="font-size:36px;line-height:38px">SUPER POWER</span></span></div>
  <a class="social-tile" href="#" style="left:706px"><span class="tile-square"></span>PAGEWAVE</a>
  <a class="social-tile" href="#" style="left:900px"><span class="tile-square"></span>PICTOLANE</a>
</section>

<section class="featured">
  <div class="photo" style="left:124px;top:68px;width:448px;height:293px;background:linear-gradient(180deg,#5fb3d8,#a9d8ea 55%,#d9b49a)" role="img" aria-label="Woman seen from behind flexing her arms against the sky"></div>
  <a class="feature" href="#" style="left:616px;top:90px">
    <div class="feature-title"><span class="title-square"></span><span><span class="title-small">FEATURED</span><span class="title-big" style="font-size:30px;line-height:34px">BRIGHT SPARROWS</span></span></div>
    <p>Vivamus porttitor purus nisi eleifend libero a tempus libero lectus feugiat felis Morbi diam mauris viverra in gravida eu mattis in ante Morbi eget arcu Morbi porta libero id ullamcorper</p>
    <p style="margin-top:6px">lacus mollis aliquam Curabitur iaculis tempus eros Curabitur vel mi sit amet magna malesuada ultrices</p>
  </a>
</section>

<footer class="site-footer">
  <div class="footer-mark"></div>
  <nav class="footer-nav"><a href="#">MISSION</a><a href="#">MANTRA</a><a href="#">MEET BS</a><a href="#">ARMOR</a></nav>
  <p class="copyright">© 2016 Company Name &nbsp;All right reserved &nbsp;Term of Use</p>
</footer>

</body>
</html>
```